Beautify our counselling web application

I have a web application in development and at the moment it is very plain.
It has being developed with laravel and vue. I need a simple design for the user interface to make it look more sleek and professional. I will need someone who is able to code the design as part of the service. The app is very low-cost for voluntary and social enterprise services and we don't have a lot of money so I need someone who is just starting out or someone with a big heart.
I have uploaded current pages to show the contents.
I will tip for good work.

Target Market(s)

Counsellors and psychotherapists

Industry/Entity Type

SaaS

Font styles to use
Serif
Sans Serif

Colors
0054AA
0677BA
7BADD7
CADEEF
E8F1F8

Requirements
Must have
• Ability to code the design into the current site
Nice to have
• elegant, modern. cool, profession. nice examples include merovaultix.com quillbanter.com fenrodu.com
Should not have
• corny literal 90s icons, icons with more than one colour using primary colours

```html
<!DOCTYPE html>
<html lang="en">
<head>
<meta charset="utf-8">
<title>Counselling App – Interface Screens</title>
<link rel="stylesheet" href="https://fonts.googleapis.com/css2?family=Poppins:wght@400;500;600;700&family=Ubuntu:wght@400;500;700&display=swap">
<style>
:root{
  --navy:#0054AA;
  --blue:#0677BA;
  --sky:#7BADD7;
  --mist:#CADEEF;
  --ice:#E8F1F8;
  --white:#FFFFFF;
  --ink:#333333;
  --line:#9AA3AD;
  --ok:#1DB37E;
}
*{box-sizing:border-box;margin:0;padding:0}
html,body{width:1200px;height:2608px;overflow:hidden;background:var(--white)}
body{position:relative;font-family:"Ubuntu",sans-serif;color:var(--ink)}

.screen{position:absolute;left:40px;width:1160px;height:786px;
  background:linear-gradient(180deg,var(--navy) 0,var(--navy) 72px,#1667B7 160px,#4A8BC8 480px,var(--sky) 100%);}
.screen--caseload{top:56px}
.screen--dashboard{top:905px}
.screen--client{top:1758px}

.brand{position:absolute;left:54px;top:24px;font-family:"Poppins",sans-serif;font-weight:700;font-size:22px;letter-spacing:-1px;color:var(--white)}
.top-actions{position:absolute;right:56px;top:24px;display:flex;gap:18px}
.top-actions svg{width:24px;height:24px;stroke:var(--white);fill:none;stroke-width:1.8;stroke-linecap:round;stroke-linejoin:round}

.sidenav{position:absolute;left:0;top:103px;width:118px;list-style:none;font-family:"Poppins",sans-serif;font-size:12px;color:var(--white)}
.sidenav li{height:34px;line-height:34px;padding-left:18px;margin-bottom:7px;border-radius:17px 0 0 17px;white-space:nowrap}
.sidenav li.is-active{background:rgba(202,222,239,.45)}

.card{position:absolute;left:118px;top:72px;width:1042px;height:654px;background:var(--white);border-radius:24px 0 0 24px}
.card--soft{background:var(--ice)}
.page-title{position:absolute;left:38px;top:26px;font-family:"Ubuntu",sans-serif;font-weight:700;font-size:20px;color:var(--navy);letter-spacing:.3px}
.page-title .crumb{color:#333}

/* caseload */
.toolbar{position:absolute;left:779px;top:23px;width:225px;height:32px;display:flex;border-radius:16px;box-shadow:0 1px 4px rgba(0,0,0,.15);overflow:hidden;font-family:"Poppins",sans-serif;font-size:9px}
.toolbar .filter{width:76px;background:var(--navy);color:var(--white);display:flex;align-items:center;justify-content:center;gap:12px}
.toolbar .search{flex:1;background:var(--white);color:#555;display:flex;align-items:center;padding-left:14px}
.caseload-table{position:absolute;left:37px;top:75px;border-collapse:collapse;table-layout:fixed;width:971px;font-size:12px;text-align:center}
.caseload-table th{height:68px;background:var(--mist);font-weight:400;font-size:12px;line-height:20px;color:#333;border:1px solid var(--line)}
.caseload-table td{height:79px;border:1px solid var(--line);color:#333}
.caseload-table .link{color:var(--navy)}
.dot{display:inline-block;width:7px;height:7px;border-radius:50%;background:var(--ok)}
.total{display:inline-flex;align-items:center;height:26px;border-radius:13px;background:var(--navy);color:var(--white);font-size:12px;padding:0 8px 0 11px;gap:7px}
.total i{width:1px;height:18px;background:rgba(255,255,255,.6)}

/* dashboard */
.welcome{position:absolute;left:380px;top:78px;width:270px;height:62px;background:var(--navy);color:var(--white);border-radius:26px 26px 4px 26px;box-shadow:3px 3px 2px rgba(0,0,0,.3);font-weight:700;font-size:17px;display:flex;align-items:center;justify-content:center;letter-spacing:.3px}
.widget{position:absolute;top:174px;width:326px;height:267px;background:var(--white);text-align:center}
.widget h2{font-size:17px;font-weight:700;color:var(--navy);letter-spacing:.3px}
.widget p{font-size:16px;color:#333;margin-top:16px}
.widget--notice{left:17px;padding-top:60px}
.widget--today{left:360px;padding-top:100px}
.widget--reviews{left:703px;padding-top:100px}
.badge{margin:14px auto 0;width:214px;height:50px;background:var(--navy);color:var(--white);border-radius:22px 22px 4px 22px;box-shadow:3px 3px 2px rgba(0,0,0,.3);font-weight:700;font-size:17px;display:flex;align-items:center;justify-content:center}
.widget--notice p{margin-top:24px}

/* client */
.tabs{position:absolute;left:38px;top:86px;display:flex;gap:18px}
.tab{width:164px;height:42px;border-radius:21px;border:2px solid #ddd;background:var(--white);color:var(--navy);font-size:15px;display:flex;align-items:center;justify-content:center;gap:8px;white-space:nowrap}
.tab--fill{background:var(--navy);color:var(--white);border-color:var(--navy);width:161px}
.episode{position:absolute;left:31px;top:177px;width:981px;height:421px;background:var(--mist)}
.episode-head{position:absolute;left:33px;top:28px;font-size:15px;color:#333}
.episode-meta{position:absolute;left:567px;top:28px;font-size:15px;color:#333}
.episode-meta span{color:var(--navy)}
.end-btn{position:absolute;left:798px;top:17px;width:133px;height:40px;border-radius:20px;background:var(--navy);color:var(--white);font-size:15px;display:flex;align-items:center;justify-content:center}
.tile{position:absolute;width:245px;height:47px;border-radius:23px;background:var(--white);display:flex;align-items:center;font-size:15px;color:var(--navy)}
.tile .ic{width:53px;height:100%;border-right:1px solid #bbb;display:flex;align-items:center;justify-content:center}
.tile .ic svg{width:30px;height:30px;stroke:var(--navy);fill:none;stroke-width:1.3;stroke-linejoin:round;stroke-linecap:round}
.tile .lb{flex:1;text-align:center}
</style>
</head>
<body>

<!-- Caseload list -->
<section class="screen screen--caseload">
  <div class="brand">COUNSELLING APP</div>
  <div class="top-actions">
    <svg viewBox="0 0 24 24"><circle cx="12" cy="12" r="10"/><path d="M9.5 9a2.5 2.5 0 1 1 3.5 2.3c-.7.3-1 .9-1 1.7"/><circle cx="12" cy="17" r=".4"/></svg>
    <svg viewBox="0 0 24 24"><circle cx="10" cy="8" r="4"/><path d="M3 21v-2a5 5 0 0 1 5-5h4"/><path d="M18 14v6M15 17h6"/></svg>
    <svg viewBox="0 0 24 24"><path d="M14 4H5v16h9"/><path d="M10 12h11M17 8l4 4-4 4"/></svg>
  </div>
  <ul class="sidenav">
    <li>DASHBOARD</li><li class="is-active">CASELOAD</li><li>CALENDER</li><li>ADDRESS BOOK</li><li>USERS</li><li>SERVICES</li><li>CLIENTS</li><li>AUDIT</li><li>MONITORING</li><li>TEMPLATES</li>
  </ul>
  <div class="card">
    <h1 class="page-title" style="top:26px">CASELOAD</h1>
    <div class="toolbar"><div class="filter">FILTER <span>&#8964;</span></div><div class="search">SEARCH....</div></div>
    <table class="caseload-table">
      <colgroup><col style="width:70px"><col style="width:70px"><col style="width:116px"><col style="width:68px"><col style="width:117px"><col style="width:68px"><col style="width:115px"><col style="width:116px"><col style="width:116px"><col style="width:115px"></colgroup>
      <tr><th>RISK</th><th>ALERTS</th><th>CLIENTS</th><th>ID</th><th>SERVICE</th><th>THERAPIST</th><th>DATE OF<br>REFERRAL</th><th>FIRST CONTACT</th><th>PREVIOUS<br>EPISODE</th><th>CONTACTS</th></tr>
      <tr><td><span class="dot"></span></td><td></td><td class="link">Owen Marlock</td><td>002</td><td class="link">Demo Service 1</td><td>Liam</td><td>05/07/2022</td><td>20/09/2022</td><td></td><td><span class="total">Total: 3<i></i>&#8250;</span></td></tr>
      <tr><td><span class="dot"></span></td><td></td><td class="link">Colin Ashgrove</td><td>003</td><td class="link">Demo Service 1</td><td>Liam</td><td>13/07/2022</td><td>20/09/2022</td><td></td><td><span class="total">Total: 2<i></i>&#8250;</span></td></tr>
      <tr><td><span class="dot"></span></td><td></td><td class="link">Helena Dorris</td><td>004</td><td class="link">Demo Service 1</td><td>Liam</td><td>19/08/2022</td><td>20/09/2022</td><td></td><td><span class="total">Total: 3<i></i>&#8250;</span></td></tr>
      <tr><td><span class="dot"></span></td><td></td><td class="link">Imogen Lark</td><td>005</td><td class="link">Demo Service 2</td><td>Dean</td><td>17/07/2022</td><td>20/09/2022</td><td></td><td><span class="total">Total: 3<i></i>&#8250;</span></td></tr>
      <tr><td></td><td></td><td class="link">Harriet Vellacott</td><td>006</td><td class="link">Demo Service 2</td><td>Dean</td><td>23/08/2022</td><td>20/09/2022</td><td>29/11/2022</td><td><span class="total">Total: 0<i></i>&#8250;</span></td></tr>
      <tr><td><span class="dot"></span></td><td></td><td class="link">Natalie Fenwick</td><td>007</td><td class="link">Demo Service 2</td><td>Dean</td><td>06/07/2022</td><td>20/09/2022</td><td></td><td><span class="total">Total: 2<i></i>&#8250;</span></td></tr>
    </table>
  </div>
</section>

<!-- Dashboard -->
<section class="screen screen--dashboard">
  <div class="brand">COUNSELLING APP</div>
  <div class="top-actions">
    <svg viewBox="0 0 24 24"><circle cx="12" cy="12" r="10"/><path d="M9.5 9a2.5 2.5 0 1 1 3.5 2.3c-.7.3-1 .9-1 1.7"/><circle cx="12" cy="17" r=".4"/></svg>
    <svg viewBox="0 0 24 24"><circle cx="10" cy="8" r="4"/><path d="M3 21v-2a5 5 0 0 1 5-5h4"/><path d="M18 14v6M15 17h6"/></svg>
    <svg viewBox="0 0 24 24"><path d="M14 4H5v16h9"/><path d="M10 12h11M17 8l4 4-4 4"/></svg>
  </div>
  <ul class="sidenav" style="top:83px">
    <li class="is-active">DASHBOARD</li><li>CASELOAD</li><li>CALENDER</li><li>ADDRESS BOOK</li><li>USERS</li><li>SERVICES</li><li>CLIENTS</li><li>AUDIT</li><li>MONITORING</li><li>TEMPLATES</li>
  </ul>
  <div class="card card--soft" style="top:69px;height:653px">
    <h1 class="page-title" style="left:18px;top:35px">DASHBOARD</h1>
    <div class="welcome">WELCOME TO DEMO</div>
    <div class="widget widget--notice"><h2>NOTIFICATIONS</h2><div class="badge">NO NOTIFICATION</div><p>No Notification</p></div>
    <div class="widget widget--today"><h2>TODAY</h2><p>No Appointments!</p></div>
    <div class="widget widget--reviews"><h2>REVIEWS</h2><p>No Reviews!</p></div>
  </div>
</section>

<!-- Client workspace -->
<section class="screen screen--client">
  <div class="brand">COUNSELLING APP</div>
  <div class="top-actions">
    <svg viewBox="0 0 24 24"><circle cx="12" cy="12" r="10"/><path d="M9.5 9a2.5 2.5 0 1 1 3.5 2.3c-.7.3-1 .9-1 1.7"/><circle cx="12" cy="17" r=".4"/></svg>
    <svg viewBox="0 0 24 24"><circle cx="10" cy="8" r="4"/><path d="M3 21v-2a5 5 0 0 1 5-5h4"/><path d="M18 14v6M15 17h6"/></svg>
    <svg viewBox="0 0 24 24"><path d="M14 4H5v16h9"/><path d="M10 12h11M17 8l4 4-4 4"/></svg>
  </div>
  <ul class="sidenav" style="top:72px">
    <li>DASHBOARD</li><li class="is-active">CASELOAD</li><li>CALENDER</li><li>ADDRESS BOOK</li><li>USERS</li><li>SERVICES</li><li>CLIENTS</li><li>AUDIT</li><li>MONITORING</li><li>TEMPLATES</li>
  </ul>
  <div class="card" style="top:70px;height:652px">
    <h1 class="page-title" style="top:40px">CASELOAD / <span class="crumb">OWEN MARLOCK</span></h1>
    <div class="tabs">
      <div class="tab tab--fill">WORKSPACE <span>&#8963;</span></div>
      <div class="tab tab--fill">CLIENT INFORMATION</div>
      <div class="tab">CLIENT RECORD</div>
      <div class="tab">CLIENT PROGRESS</div>
      <div class="tab">PAYMENTS</div>
    </div>
    <div class="episode">
      <div class="episode-head">EPISODE 1</div>
      <div class="episode-meta">STARTED: <span>WED SEP 14 2022</span> &nbsp;&#8963;</div>
      <div class="end-btn">END EPISODE</div>

      <div class="tile" style="left:71px;top:78px"><div class="ic"><svg viewBox="0 0 30 30"><rect x="6" y="5" width="15" height="20" rx="1"/><path d="M9 10h9M9 14h9M9 18h5M17 24l8-8 2 2-8 8h-2z"/></svg></div><div class="lb">SESSION REORD</div></div>
      <div class="tile" style="left:355px;top:78px"><div class="ic"><svg viewBox="0 0 30 30"><rect x="5" y="4" width="18" height="22" rx="1"/><circle cx="15" cy="15" r="5"/><path d="M19 19l6 6M8 8h12"/></svg></div><div class="lb">ASSESSMENT</div></div>
      <div class="tile" style="left:644px;top:78px"><div class="ic"><svg viewBox="0 0 30 30"><path d="M15 4l11 21H4z"/><path d="M15 11v7M15 21v1"/></svg></div><div class="lb">RISK MANAGEMENT</div></div>

      <div class="tile" style="left:71px;top:147px"><div class="ic"><svg viewBox="0 0 30 30"><rect x="6" y="5" width="18" height="21" rx="1"/><path d="M11 3h8v4h-8zM10 12h10M10 16h10M10 20h6"/></svg></div><div class="lb">TREATMENT PLAN</div></div>
      <div class="tile" style="left:355px;top:147px"><div class="ic"><svg viewBox="0 0 30 30"><path d="M15 4l9 3v7c0 6-4 10-9 12-5-2-9-6-9-12V7z"/><path d="M10 15l4 4 6-7"/></svg></div><div class="lb">SAFEGUARDING</div></div>
      <div class="tile" style="left:644px;top:147px"><div class="ic"><svg viewBox="0 0 30 30"><rect x="12" y="4" width="14" height="18" rx="1"/><path d="M15 9h8M15 13h8M15 17h5"/><circle cx="8" cy="18" r="3"/><path d="M3 27c0-3 2-5 5-5s5 2 5 5"/></svg></div><div class="lb">CONSENT</div></div>

      <div class="tile" style="left:71px;top:215px"><div class="ic"><svg viewBox="0 0 30 30"><rect x="6" y="5" width="18" height="21" rx="1"/><path d="M11 3h8v4h-8z"/><circle cx="15" cy="16" r="5"/><path d="M13.5 14.5a1.6 1.6 0 1 1 2 1.5v1M15 19v.3"/></svg></div><div class="lb">QUESTIONNAIRE</div></div>
      <div class="tile" style="left:355px;top:215px"><div class="ic"><svg viewBox="0 0 30 30"><path d="M9 4h11l5 5v17H9z"/><path d="M20 4v5h5M12 13h10M12 17h10M12 21h7M5 8v19h15"/></svg></div><div class="lb">DOCUMENT</div></div>
      <div class="tile" style="left:644px;top:215px"><div class="ic"><svg viewBox="0 0 30 30"><rect x="12" y="4" width="14" height="18" rx="1"/><path d="M15 9h8M15 13h8M15 17h5"/><circle cx="8" cy="18" r="3"/><path d="M3 27c0-3 2-5 5-5s5 2 5 5"/></svg></div><div class="lb">NON-CLINICAL NOTE</div></div>

      <div class="tile" style="left:71px;top:287px"><div class="ic"><svg viewBox="0 0 30 30"><path d="M7 4h12l5 5v17H7z"/><circle cx="15" cy="15" r="4"/><path d="M18 18l4 4M10 23h6"/></svg></div><div class="lb">SUMMARY</div></div>
      <div class="tile" style="left:359px;top:287px"><div class="ic"><svg viewBox="0 0 30 30"><rect x="4" y="6" width="22" height="20" rx="1"/><path d="M4 11h22M10 4v4M20 4v4M9 15h2M14 15h2M19 15h2M9 20h2M14 20h2M19 20h2"/></svg></div><div class="lb">TIMELINE</div></div>
    </div>
  </div>
</section>

</body>
</html>
```